Kestrel Facilities Business Card Design

We would now like to design business cards with the new Kestrel Facilities logo

Target Market(s)

Professional

Industry/Entity Type

Professional services

Contact Information for Business Card

Employee name, title, phone number, email address, corporate office address and logo.

Font styles to use
Sans Serif

Colors
0054AA
0677BA
7BADD7
CADEEF
E8F1F8

Requirements
Must have
• My logo
Should not have
• any other pictures or images besides my logo

```html
<!DOCTYPE html>
<html lang="en">
<head>
<meta charset="utf-8">
<title>Kestrel Facilities – Business Cards</title>
<link rel="stylesheet" href="https://fonts.googleapis.com/css2?family=Arimo:wght@400;700&family=Roboto+Condensed:wght@600&display=swap">
<style>
  :root {
    --bg: #2a2a2a;
    --brand-blue: #0a80e6;
    --brand-deep: #0054aa;
    --ink: #1c1c1c;
    --paper: #ffffff;
    --rule: #9a9a9a;
  }
  * { margin: 0; padding: 0; box-sizing: border-box; }
  html, body { width: 1200px; height: 1015px; overflow: hidden; }
  body {
    background: var(--bg);
    font-family: "Arimo", Arial, sans-serif;
    display: flex;
    flex-direction: column;
    align-items: center;
    justify-content: center;
    gap: 50px;
  }
  .card {
    width: 700px;
    height: 400px;
    position: relative;
    box-shadow: 0 10px 30px rgba(0,0,0,.5);
  }
  .card--front {
    background: var(--brand-blue);
    display: flex;
    align-items: center;
    justify-content: center;
  }
  .card--back { background: var(--paper); }

  .wordmark {
    display: flex;
    align-items: center;
    gap: 16px;
    font-family: "Roboto Condensed", Arial, sans-serif;
    font-weight: 600;
    text-transform: uppercase;
    letter-spacing: 2px;
  }
  .wordmark__square { width: 46px; height: 46px; }
  .wordmark__name { font-size: 44px; line-height: 1; }
  .card--front .wordmark { color: var(--paper); }
  .card--front .wordmark__square { background: var(--paper); }

  .card--back .wordmark {
    position: absolute;
    right: 50px;
    top: 90px;
    color: var(--brand-blue);
  }
  .card--back .wordmark__square { background: var(--brand-blue); width: 36px; height: 36px; }
  .card--back .wordmark__name { font-size: 34px; }

  .divider {
    position: absolute;
    left: 40px;
    right: 40px;
    top: 222px;
    height: 1px;
    background: var(--rule);
  }
  .person {
    position: absolute;
    left: 40px;
    top: 150px;
  }
  .person__name {
    font-family: "Roboto Condensed", Arial, sans-serif;
    font-weight: 600;
    font-size: 36px;
    color: var(--brand-blue);
    text-transform: uppercase;
    line-height: 1;
  }
  .person__title { font-size: 22px; color: var(--ink); margin-top: 4px; }

  .contact {
    position: absolute;
    left: 40px;
    top: 240px;
    list-style: none;
    font-size: 24px;
    color: var(--ink);
    line-height: 38px;
  }
  .contact__item { display: flex; align-items: center; gap: 12px; }
  .contact__icon { width: 22px; height: 22px; flex: none; }
  .contact__accent { color: var(--brand-blue); }

  .address {
    position: absolute;
    right: 40px;
    top: 244px;
    text-align: right;
    font-style: normal;
    font-size: 21px;
    line-height: 28px;
    color: var(--ink);
  }
</style>
</head>
<body>
  <section class="card card--front" aria-label="Business card front">
    <div class="wordmark">
      <span class="wordmark__square"></span>
      <span class="wordmark__name">Kestrel Facilities</span>
    </div>
  </section>

  <section class="card card--back" aria-label="Business card back">
    <div class="wordmark">
      <span class="wordmark__square"></span>
      <span class="wordmark__name">Kestrel Facilities</span>
    </div>

    <div class="person">
      <h1 class="person__name">Daniel Harper</h1>
      <p class="person__title">Managing Director</p>
    </div>

    <div class="divider"></div>

    <ul class="contact">
      <li class="contact__item">
        <svg class="contact__icon" viewBox="0 0 24 24" aria-hidden="true"><path fill="#0a80e6" d="M6.6 10.8a15.1 15.1 0 0 0 6.6 6.6l2.2-2.2a1 1 0 0 1 1-.25 11.4 11.4 0 0 0 3.6.57 1 1 0 0 1 1 1V20a1 1 0 0 1-1 1A17 17 0 0 1 3 4a1 1 0 0 1 1-1h3.5a1 1 0 0 1 1 1c0 1.25.2 2.45.57 3.57a1 1 0 0 1-.25 1z"/></svg>
        044-555 018 274
      </li>
      <li class="contact__item">
        <svg class="contact__icon" viewBox="0 0 24 24" aria-hidden="true"><rect x="2" y="5" width="20" height="14" fill="#0a80e6"/><path d="M2 5l10 8 10-8" fill="none" stroke="#fff" stroke-width="1.8"/></svg>
        info@kestrelfm.com
      </li>
      <li class="contact__item">
        <svg class="contact__icon" viewBox="0 0 24 24" aria-hidden="true"><g fill="none" stroke="#0a80e6" stroke-width="1.8"><circle cx="12" cy="12" r="9.5"/><ellipse cx="12" cy="12" rx="4" ry="9.5"/><path d="M2.5 12h19M4 7h16M4 17h16"/></g></svg>
        <span>www.<span class="contact__accent">kestrelfm</span>.com</span>
      </li>
    </ul>

    <address class="address">
      18 Harbour Row, Suite 4<br>
      30217, Eastvale
    </address>
  </section>
</body>
</html>
```